School Poster

Design so that these can be placed in classrooms across the school.

Attached is another design we have had done. Use a similar theme.

Consider using themes from https://corvalhs.edq.example.au/

please edit Binder1 doc.

Students and teachers

```html
<!DOCTYPE html>
<html lang="en">
<head>
<meta charset="utf-8">
<title>Corval SHS Classroom Posters</title>
<link href="https://fonts.googleapis.com/css2?family=Archivo+Black&family=Arimo:ital,wght@0,400;0,700;1,400;1,700&display=swap" rel="stylesheet">
<style>
  :root {
    --navy: #243a7c;
    --navy-deep: #1e3a8e;
    --yellow: #f3e64c;
    --gold: #fdd65c;
    --lavender: #e3e3f3;
    --lavender-dark: #c6c6e4;
    --cream: #fbf8dc;
    --cream-dark: #f6f0ba;
    --ink: #1a1a1a;
    --white: #ffffff;
    --backdrop: #b4b4b4;
  }
  * { box-sizing: border-box; margin: 0; padding: 0; }
  html, body { width: 1200px; height: 1200px; overflow: hidden; }
  body { background: var(--backdrop); font-family: "Arimo", Arial, sans-serif; color: var(--ink); position: relative; }

  .poster { position: absolute; top: 240px; width: 511px; height: 719px; background: var(--white); overflow: hidden; }
  .poster--steps { left: 74px; }
  .poster--ai { left: 622px; }

  .header-band { position: absolute; left: 0; top: 0; width: 511px; height: 152px; }
  .school-mark { position: absolute; left: 22px; top: 50px; width: 104px; display: flex; align-items: center; gap: 6px; }
  .school-mark__dot { width: 14px; height: 14px; border-radius: 50%; background: var(--yellow); flex: none; }
  .school-mark__name { font-family: "Arimo", Arial, sans-serif; font-weight: 700; font-size: 17px; line-height: 1.1; color: var(--white); }

  .kicker { position: absolute; left: 136px; top: 14px; font-weight: 700; font-size: 19px; color: var(--white); letter-spacing: 0.2px; white-space: nowrap; }
  .headline { position: absolute; left: 134px; font-family: "Archivo Black", Arial, sans-serif; color: var(--yellow); line-height: 1; white-space: nowrap; }
  .headline--steps { top: 38px; font-size: 44px; line-height: 41px; }
  .headline--ai { left: 137px; top: 33px; font-size: 30px; line-height: 35px; }
  .headline .white { color: var(--white); }

  /* Steps */
  .step { position: absolute; left: 24px; width: 462px; }
  .step__tab { position: absolute; left: 0; top: 0; height: 20px; padding-right: 11px; border: 1.5px solid var(--navy); border-radius: 0 12px 12px 0; display: flex; align-items: center; white-space: nowrap; font-family: "Archivo Black", Arial, sans-serif; font-size: 13px; letter-spacing: 0.2px; z-index: 2; }
  .step__num { flex: none; width: 20px; height: 20px; margin-left: -1.5px; border: 1.5px solid var(--navy); border-radius: 0 10px 10px 0; background: var(--white); color: var(--navy); font-family: "Arimo", Arial, sans-serif; font-weight: 700; font-size: 13px; display: flex; align-items: center; justify-content: center; margin-right: 7px; }
  .step__tab--gold { background: var(--gold); color: var(--navy); }
  .step__tab--navy { background: var(--navy-deep); color: var(--white); border-color: var(--gold); }
  .step__tab--navy .step__num { border-color: var(--gold); }
  .step__box { position: absolute; left: 0; width: 462px; border: 1.5px solid var(--navy); border-radius: 0 8px 8px 8px; display: flex; overflow: hidden; }
  .step__box--cream { border-color: var(--gold); background: var(--cream); }
  .step__box--lav { background: var(--lavender); }
  .step__panel { width: 155px; flex: none; display: flex; flex-direction: column; align-items: center; justify-content: center; gap: 6px; border-right: 2px dotted var(--navy); text-align: center; font-style: italic; font-weight: 700; font-size: 14.5px; line-height: 17px; }
  .step__panel--gold { background: var(--gold); color: var(--navy-deep); }
  .step__panel--navy { background: var(--navy-deep); color: var(--white); border-right-color: var(--gold); }
  .step__list { list-style: none; flex: 1; padding-top: 16px; }
  .step__list li { height: 22px; display: flex; align-items: center; padding-left: 15px; font-size: 14px; white-space: nowrap; }
  .step__list li::before { content: ""; flex: none; width: 4px; height: 4px; border-radius: 50%; background: var(--navy-deep); margin-right: 9px; }
  .step__box--lav .step__list li:nth-child(odd) { background: var(--lavender-dark); }
  .step__box--cream .step__list li:nth-child(odd) { background: var(--cream-dark); }
  .step__note { font-style: italic; font-size: 14px; padding: 19px 0 0 15px; white-space: nowrap; }

  .footer-band { position: absolute; left: 0; top: 685px; width: 511px; height: 20px; background: var(--navy); }
  .footer-pill { position: absolute; top: 683px; height: 23px; background: var(--yellow); border-radius: 12px; display: flex; align-items: center; justify-content: center; color: var(--navy-deep); font-weight: 700; white-space: nowrap; }
  .footer-pill--steps { left: 88px; width: 333px; font-size: 13.5px; letter-spacing: 2px; }
  .footer-pill--ai { left: 24px; width: 463px; font-size: 10.5px; letter-spacing: 0.6px; }

  /* AI rules */
  .rule-box { position: absolute; left: 104px; width: 391px; background: var(--cream); border: 1.5px solid var(--navy); border-radius: 6px; }
  .rule-box::before { content: ""; position: absolute; left: 101px; top: 8px; bottom: 8px; border-left: 2px dotted var(--gold); }
  .rule-list { list-style: none; position: absolute; left: 112px; right: 10px; top: 4px; bottom: 4px; display: flex; flex-direction: column; }
  .rule-list li { flex: 1; display: flex; align-items: center; padding-left: 13px; position: relative; font-size: 14px; line-height: 16.5px; border-bottom: 1px solid var(--gold); }
  .rule-list li:last-child { border-bottom: none; }
  .rule-list li::before { content: ""; position: absolute; left: 1px; top: 50%; margin-top: -2px; width: 4.5px; height: 4.5px; border-radius: 50%; background: var(--navy-deep); }
  .rule-list li.two-line::before { top: 13px; }
  .rule-label { position: absolute; left: 14px; width: 179px; background: var(--navy); border-radius: 6px; color: var(--white); font-weight: 700; font-size: 13.5px; line-height: 16.5px; text-align: center; display: flex; align-items: flex-end; justify-content: center; padding-bottom: 10px; }
  .rule-badge { position: absolute; left: 81px; width: 44px; height: 44px; border-radius: 50%; background: var(--gold); border: 1.5px solid var(--white); }
</style>
</head>
<body>

<section class="poster poster--steps">
  <svg class="header-band" viewBox="0 0 511 152" aria-hidden="true">
    <rect width="511" height="152" fill="var(--navy)"/>
    <path d="M0 139 Q200 118 330 128 L330 152 L0 152 Z" fill="var(--yellow)"/>
    <path d="M0 144 Q230 112 511 149 L511 152 L0 152 Z" fill="var(--white)"/>
  </svg>
  <div class="school-mark"><span class="school-mark__dot"></span><span class="school-mark__name">CORVAL SHS</span></div>
  <p class="kicker">BEFORE YOU ASK THE TEACHER.....</p>
  <h1 class="headline headline--steps">TRY THESE<br>STEPS FIRST!</h1>

  <div class="step" style="top:162px;">
    <div class="step__tab step__tab--gold"><span class="step__num">1</span>THINK FIRST</div>
    <div class="step__box step__box--lav" style="top:9px;height:108px;">
      <div class="step__panel step__panel--gold">
        <svg width="36" height="36" viewBox="0 0 36 36" fill="none" stroke="var(--navy-deep)" stroke-width="1.8" aria-hidden="true">
          <path d="M10 33v-6c-4-2-6-6-6-11C4 8 10 3 18 3s13 5 13 12c0 3-1 5-3 7v4h-4v7"/>
          <circle cx="19" cy="14" r="4"/><circle cx="19" cy="14" r="7" stroke-dasharray="3 2"/>
        </svg>
        <span>Don’t give up<br>straight away</span>
      </div>
      <ul class="step__list">
        <li>Read the question carefully</li>
        <li>Identify what you already know</li>
        <li>Try a strategy you’ve used before</li>
        <li>Give yourself thinking time</li>
      </ul>
    </div>
  </div>

  <div class="step" style="top:312px;">
    <div class="step__tab step__tab--navy"><span class="step__num">2</span>CHECK YOUR SUPPORTS</div>
    <div class="step__box step__box--cream" style="top:10px;height:152px;">
      <div class="step__panel step__panel--navy">
        <svg width="34" height="36" viewBox="0 0 34 36" fill="none" stroke="var(--white)" stroke-width="1.8" aria-hidden="true">
          <path d="M10 3h13l7 7v23H10z"/><path d="M23 3v7h7"/>
          <path d="M15 16h10M15 21h10M17 26h8"/>
          <circle cx="9" cy="27" r="6" fill="var(--navy-deep)"/><path d="M6 27l2 2 4-4"/>
        </svg>
        <span style="margin-top:14px;">Before asking<br>for help, check:</span>
      </div>
      <ul class="step__list" style="padding-top:7px;">
        <li>Learning goal and success criteria</li>
        <li>Worked examples</li>
        <li>Class notes</li>
        <li>Classroom displays</li>
        <li>LearnHub resources</li>
        <li>Task sheet and instructions</li>
      </ul>
    </div>
  </div>

  <div class="step" style="top:507px;">
    <div class="step__tab step__tab--gold"><span class="step__num">3</span>ASK 3 BEFORE ME</div>
    <div class="step__box step__box--lav" style="top:11px;height:127px;">
      <div class="step__panel step__panel--gold">
        <svg width="38" height="32" viewBox="0 0 38 32" fill="none" stroke="var(--navy-deep)" stroke-width="1.8" aria-hidden="true">
          <path d="M2 2h20v14H9l-5 4v-4H2z"/>
          <path d="M14 10h22v16h-2v4l-5-4H14z" fill="var(--gold)"/>
          <path d="M18 15h14M18 19h14M18 23h10"/>
        </svg>
        <span>Ask three sources<br>before asking the<br>teacher:</span>
      </div>
      <div style="flex:1;">
        <ul class="step__list" style="padding-top:16px;">
          <li>A person (partner or neighbour)</li>
          <li>A place (notes, display, LearnHub)</li>
          <li>A resource (worked example, task sheet)</li>
        </ul>
        <p class="step__note">Then ask the teacher if you still need help</p>
      </div>
    </div>
  </div>

  <div class="footer-band"></div>
  <div class="footer-pill footer-pill--steps">WE BELIEVE. WE STRIVE. WE ACHIEVE</div>
</section>

<section class="poster poster--ai">
  <svg class="header-band" viewBox="0 0 511 152" aria-hidden="true">
    <rect width="511" height="152" fill="var(--navy)"/>
    <path d="M0 139 Q200 118 330 128 L330 152 L0 152 Z" fill="var(--yellow)"/>
    <path d="M0 144 Q230 112 511 149 L511 152 L0 152 Z" fill="var(--white)"/>
  </svg>
  <div class="school-mark"><span class="school-mark__dot"></span><span class="school-mark__name">CORVAL SHS</span></div>
  <h1 class="headline headline--ai">USING AI AND OTHER<br>TOOLS <span class="white">RESPONSIBLY</span></h1>

  <div class="rule-box" style="top:159px;height:158px;">
    <ul class="rule-list">
      <li>Complete your own work</li>
      <li class="two-line">Demonstrate your progress (drafts, notes, planning, revisions)</li>
      <li>Use feedback to improve your work</li>
      <li class="two-line">Demonstrate your understanding of the ideas in your submission</li>
    </ul>
  </div>
  <div class="rule-label" style="top:221px;height:55px;">WHAT YOU MUST DO</div>
  <svg class="rule-badge" style="top:199px;" viewBox="0 0 44 44" aria-hidden="true"><path d="M12 22l7 7 14-14" fill="none" stroke="var(--navy-deep)" stroke-width="5" stroke-linecap="round"/></svg>

  <div class="rule-box" style="top:326px;height:157px;">
    <ul class="rule-list">
      <li>Brainstorm ideas</li>
      <li>Check spelling, grammar and clarity</li>
      <li class="two-line">Read your work aloud using<br>text-to-speech tools</li>
      <li class="two-line">Help identify areas for improvement in a draft</li>
    </ul>
  </div>
  <div class="rule-label" style="top:373px;height:85px;">WHAT AI CAN HELP YOU DO (WHEN APPROVED BY YOUR TEACHER)</div>
  <svg class="rule-badge" style="top:351px;" viewBox="0 0 44 44" aria-hidden="true"><path d="M12 22l7 7 14-14" fill="none" stroke="var(--navy-deep)" stroke-width="5" stroke-linecap="round"/></svg>

  <div class="rule-box" style="top:493px;height:174px;">
    <ul class="rule-list">
      <li>Submit AI generated work as your own</li>
      <li class="two-line">Copy and paste AI responses without acknowledging or adapting them</li>
      <li class="two-line">Use AI tools to complete the whole task for you</li>
      <li class="two-line">Submit work that does not demonstrate your understanding</li>
    </ul>
  </div>
  <div class="rule-label" style="top:564px;height:55px;">WHAT YOU CANNOT DO</div>
  <svg class="rule-badge" style="top:542px;" viewBox="0 0 44 44" aria-hidden="true"><path d="M14 14l16 16M30 14L14 30" fill="none" stroke="var(--navy-deep)" stroke-width="5" stroke-linecap="round"/></svg>

  <div class="footer-band"></div>
  <div class="footer-pill footer-pill--ai">IF YOU DIDN’T CREATE, DEVELOP AND UNDERSTAND IT, IT ISN’T YOUR WORK.</div>
</section>

</body>
</html>
```